Tovel & Associates - London New Letting and Property Management Company *

Tovel & Associates LTD is a new company based in London, and works with brand new residential property in the city centre.

We are aiming to have 1000 new properties a year.

We are looking for something modern and minimalistic :
Logo ,Monogram, Paper Head and Business Card.

Target Market(s)

Internation landlords

Industry/Entity Type

Real Estate

Logo Text

Tovel & Associates

Colors

Designer to choose colors to be used in the design.

Requirements
Nice to have
• A particular monogram with "TA"
Should not have
• Little House over the logo

```html
<!DOCTYPE html>
<html lang="en">
<head>
<meta charset="utf-8">
<title>Tovel &amp; Associates — Business Card</title>
<link href="https://fonts.googleapis.com/css2?family=Montserrat:wght@400;500;700&display=swap" rel="stylesheet">
<style>
  :root {
    --backdrop: #2b2624;
    --card: #1b1c1e;
    --card-edge: #24262a;
    --accent: #2196d9;
    --ink: #ffffff;
    --silver: #8d8f93;
  }
  * { margin: 0; padding: 0; box-sizing: border-box; }
  html, body {
    width: 1200px; height: 715px; overflow: hidden;
    background: var(--backdrop);
    font-family: "Montserrat", Arial, sans-serif;
  }
  .canvas {
    position: relative; width: 1200px; height: 715px;
    display: flex; align-items: center; justify-content: center; gap: 48px;
  }
  .card {
    position: relative; width: 525px; height: 300px;
    background: var(--card);
    border-radius: 4px;
    box-shadow: 0 18px 40px rgba(0,0,0,.55);
  }
  .card--front { border-bottom: 5px solid var(--accent); }
  .front-name {
    position: absolute; inset: 0;
    display: flex; align-items: center; justify-content: center;
    color: var(--silver); font-weight: 500; font-size: 30px; letter-spacing: .5px;
  }
  .card--back { display: flex; align-items: center; padding: 0 34px; }
  .brand {
    width: 215px; display: flex; align-items: center; gap: 10px;
    color: var(--ink); font-weight: 500; font-size: 20px; line-height: 1.25;
  }
  .brand-square { width: 14px; height: 14px; background: var(--accent); flex: none; }
  .divider { width: 2px; height: 190px; background: var(--accent); margin: 0 24px; }
  .details { color: var(--ink); font-size: 13.5px; line-height: 1.45; }
  .person-name { color: var(--accent); font-weight: 700; font-size: 17px; text-transform: uppercase; line-height: 1.1; }
  .person-role { color: var(--accent); font-size: 13px; margin-bottom: 10px; }
  .contact-row { display: flex; align-items: center; gap: 8px; }
  .contact-row svg { width: 11px; height: 11px; flex: none; }
  .web-domain { color: var(--accent); }
  .address { margin-top: 6px; }
</style>
</head>
<body>
<main class="canvas">
  <section class="card card--front">
    <div class="front-name">Tovel &amp; Associates</div>
  </section>

  <section class="card card--back">
    <div class="brand">
      <span class="brand-square"></span>
      <span>Tovel &amp; Associates LTD</span>
    </div>
    <div class="divider"></div>
    <div class="details">
      <p class="person-name">Daniel Hart</p>
      <p class="person-role">Founder</p>
      <p class="contact-row">
        <svg viewBox="0 0 12 12"><rect x="3" y="0.5" width="6" height="11" rx="1" fill="none" stroke="#fff"/></svg>
        407. 555. 0148
      </p>
      <p class="contact-row">
        <svg viewBox="0 0 12 12"><path d="M2 1l2.5 0 1 3-1.5 1a7 7 0 0 0 3 3l1-1.5 3 1V11A9 9 0 0 1 1 2z" fill="#fff"/></svg>
        407. 555. 0190
      </p>
      <p class="contact-row">
        <svg viewBox="0 0 12 12"><rect x="0.5" y="2.5" width="11" height="7" fill="none" stroke="#fff"/><path d="M0.5 2.5L6 7l5.5-4.5" fill="none" stroke="#fff"/></svg>
        info@tovelassociates.com
      </p>
      <p class="contact-row">
        <svg viewBox="0 0 12 12"><circle cx="6" cy="6" r="5.3" fill="none" stroke="#fff"/><path d="M0.7 6h10.6M6 0.7c-3 3-3 7.6 0 10.6M6 0.7c3 3 3 7.6 0 10.6" fill="none" stroke="#fff" stroke-width=".8"/></svg>
        <span>www.<span class="web-domain">tovelassociates</span>.com</span>
      </p>
      <p class="address">48 Harrow Lane<br>Kingsford, FL 32900</p>
    </div>
  </section>
</main>
</body>
</html>
```